KRV Boltmaster Manufacturer New Web Design

We need a new theme designed for metal fastener manufacturing company, KRV Boltmaster Group, a $60M division of Marrowfield Forge Holdings, Inc. We manufacture screw, pins and washers to industrial customers (non-Automotive) such as HN Homeware, Paul Brenner, LUX, Venmora, etc. Our current website is www.boltmaster.example. We would like to stick with the same logo/color scheme, however, I'm aiming to modernize the website's look and feel.

Here are some of our competitor's websites:
- https://www.torvalink.example/
- http://glenrivet.example/
- http://www.harlowbuiltjoining.example/
- http://lugsandcustoms.example/
- http://www.dunmerebolt.example/

Target Market(s)

We primarily want to target engineers working in the following markets:
- Appliance (HN Homeware, Frostavel)
- Ag (Brenner, LUX)
- Recreational Vehicle (Venmora, Tundra Fox)
- Outdoor Power (Brellvik, Pask)

We secondarily want to target buyers working at the above markets as well as buyers at Fastener distributors such as Boltique, Parts Dynamics, Kessel Fordham.

Industry/Entity Type

Metal Forging

Number of Pages Required

1 page

Requirements
Must have
• For products: "Threaded" product as the primary focus. "Pins" product is the secondary focus, followed by all others.
• Please use same logo and color scheme as I do not plan to change.
Nice to have
• Highlight our featured proprietary products (pamphlets attached). KRV Boltmaster's GRIP-N, KelDrive, Boltmaster Coil, Avalanche.

```html
<!DOCTYPE html>
<html lang="en">
<head>
<meta charset="utf-8">
<title>KRV Boltmaster Group</title>
<link rel="stylesheet" href="https://fonts.googleapis.com/css2?family=Source+Sans+3:wght@400;600;700&display=swap">
<style>
  :root{
    --sky:#acd8f0;
    --page:#ccfffc;
    --ink:#000;
    --charcoal:#333;
    --slate:#666;
    --tile:#999;
    --navy:#0a4a78;
    --royal:#1a4fa8;
    --bright:#1c63c0;
    --button:#1f5ea8;
    --muted:#6b6b6b;
    --foot:#f4f4f4;
    --band:#00476e;
    --rose:#e0476b;
    --dot:#bdbdbd;
    --price:#3aa8c8;
  }
  *{margin:0;padding:0;box-sizing:border-box}
  html,body{width:672px;height:1200px;overflow:hidden}
  body{position:relative;background:var(--sky);font-family:"Source Sans 3",Arial,sans-serif;color:var(--ink)}
  .abs{position:absolute}
  .page{left:110px;top:0;width:452px;height:1023px;background:var(--page)}

  .brand{left:124px;top:40px;display:flex;align-items:center;gap:6px}
  .brand-mark{width:28px;height:28px;border-radius:50%;background:var(--royal)}
  .brand-name{font-size:17px;font-weight:600;color:var(--royal)}

  .nav a{position:absolute;top:56px;font-size:9px;color:var(--royal);text-decoration:none}
  .nav a.current{color:var(--ink)}

  .hero{left:110px;top:106px;width:336px;height:269px;background:var(--ink);color:#fff}
  .hero h1{position:absolute;left:20px;top:30px;font-size:26px;font-weight:400;line-height:35px}
  .hero p{position:absolute;left:20px;top:98px;width:215px;font-size:12px;font-weight:600;line-height:18.4px}
  .hero .buy-now{position:absolute;left:16px;top:184px;width:98px;height:34px;background:var(--button);color:#fff;font-size:14px;display:flex;align-items:center;justify-content:center}
  .hero .dots{position:absolute;left:32px;top:226px;display:flex;gap:9px}
  .hero .dots i{width:8px;height:8px;border-radius:50%;background:#8c8c8c}
  .hero .dots i.on{background:#fff}

  .news{left:456px;top:106px;width:106px;color:#fff}
  .news-top{height:134px;background:var(--ink);padding:9px 6px}
  .news-top h2{font-size:10.5px;font-weight:400;margin-bottom:7px}
  .news p{font-size:5.6px;font-weight:600;line-height:8.7px;padding-left:9px;width:94px}
  .news-bottom{height:134px;background:var(--charcoal);padding-top:46px;padding-left:6px}

  .feature{top:394px;height:134px;background:var(--slate);color:#fff}
  .feature .placeholder{position:absolute;font-size:16px;line-height:20px;top:18px}
  .feature .tag{position:absolute;left:16px;top:97px;width:69px;height:20px;background:var(--navy);font-size:8px;font-weight:600;display:flex;align-items:center;justify-content:center}

  .section-title{left:118px;top:561px;font-size:10.5px;color:var(--royal)}
  .mini-dots{left:216px;top:566px;display:flex;gap:5px}
  .mini-dots i{width:5px;height:5px;border-radius:50%;background:var(--dot)}
  .mini-dots i.on{background:var(--navy)}

  .product{top:617px;width:100px;text-align:center}
  .product .thumb{margin:0 auto;width:58px;height:50px;background:var(--tile);color:#fff;font-size:8px;font-weight:600;line-height:14px;display:flex;align-items:center;justify-content:center}
  .product .name{margin-top:14px;font-size:8px;color:var(--royal)}
  .product .stars{margin-top:3px;height:9px}
  .product .order{margin-top:6px;display:flex;justify-content:center;align-items:center;gap:6px}
  .product .price{font-size:7.5px;color:var(--price)}
  .product .buy{width:44px;height:13px;background:var(--navy);color:#fff;font-size:7px;font-weight:700;display:flex;align-items:center;justify-content:center}

  .intro{left:110px;top:766px;width:452px;text-align:center}
  .intro h2{font-size:21px;font-weight:400;color:#444}
  .intro p{margin:6px auto 0;width:300px;font-size:12px;line-height:17.5px;color:var(--muted)}

  .circle{top:855px;width:119px;height:119px;border-radius:50%;background:var(--ink);display:flex;align-items:center;justify-content:center;text-align:center;font-size:16px;line-height:26px}
  .circle.blue{color:var(--bright)}
  .circle.white{color:#fff}

  .footer{left:0;top:1023px;width:672px;height:139px;background:var(--foot)}
  .foot-col{top:1037px}
  .foot-col h3{font-size:14px;font-weight:400;color:var(--muted)}
  .foot-col h3 span{color:var(--royal)}
  .foot-col .rule{width:30px;height:1px;background:var(--rose);margin-top:2px}
  .foot-col p{margin-top:10px;width:134px;font-size:7.5px;line-height:13.6px;color:#555}
  .links{margin-top:9px;display:grid;grid-template-columns:58px 58px;row-gap:5px;font-size:7px;color:var(--muted)}
  .social{margin-top:8px;display:flex;gap:4px}
  .social i{width:15px;height:15px;border-radius:50%;border:1px solid #333}

  .legal{left:0;top:1162px;width:672px;height:38px;background:var(--band);color:#fff;font-size:7.4px;font-weight:600;line-height:12px;text-align:center;padding-top:6px}
</style>
</head>
<body>
  <div class="abs page"></div>

  <header>
    <div class="abs brand"><span class="brand-mark"></span><span class="brand-name">KRV Boltmaster</span></div>
    <nav class="nav">
      <a class="current" style="left:329px">HOME</a>
      <a style="left:363px">Products</a>
      <a style="left:404px">Engineering</a>
      <a style="left:456px">About Us</a>
      <a style="left:495px">Contact Us</a>
    </nav>
  </header>

  <section class="abs hero">
    <h1>Better Fastners for<br>Better Products</h1>
    <p>Lorem ipsum dolor sit amet, consectetur adipisicing elit, sed do eiusmod tempor incididunt ut labore et dolore. magna aliqua. Ut enim ad minim</p>
    <div class="buy-now">BUY NOW</div>
    <div class="dots"><i></i><i class="on"></i><i></i><i></i></div>
  </section>

  <aside class="abs news">
    <div class="news-top">
      <h2>NEWS AND EVENTS</h2>
      <p style="padding-left:10px">Eiusmod tempor incididunt ut labore et dolore magna aliqua. Ut enim ad minim veniam, quis nostrud exerc itation ullam.</p>
    </div>
    <div class="news-bottom">
      <p style="padding-left:9px">Go laboris nisi ut aliquip ex ea commodo consequat. Duis aute irure dolor in reprehenderit in voluptate velit esse. cillum dolore eu fugiat nulla</p>
    </div>
  </aside>

  <section class="abs feature" style="left:110px;width:221px" role="img" aria-label="Threaded fastener product photo">
    <div class="placeholder" style="left:52px">PUT IMAGE<br>HERE</div>
    <div class="tag">THREADED</div>
  </section>
  <section class="abs feature" style="left:342px;width:220px" role="img" aria-label="Pins product photo">
    <div class="placeholder" style="left:85px">PUT IMAGE<br>HERE</div>
    <div class="tag">PINS</div>
  </section>

  <h2 class="abs section-title" style="font-weight:400">OUR PRODUCTS</h2>
  <div class="abs mini-dots"><i></i><i class="on"></i><i></i><i></i></div>

  <svg class="abs" style="left:110px;top:634px" width="452" height="30" viewBox="0 0 452 30">
    <polyline points="15,0 0,15 15,30" fill="none" stroke="#777" stroke-width="1"/>
    <polyline points="436,0 451,15 436,30" fill="none" stroke="#777" stroke-width="1"/>
  </svg>

  <svg width="0" height="0" style="position:absolute">
    <defs><symbol id="star" viewBox="0 0 10 10"><polygon points="5,0.5 6.3,3.6 9.6,3.8 7,6 7.9,9.3 5,7.5 2.1,9.3 3,6 0.4,3.8 3.7,3.6"/></symbol></defs>
  </svg>

  <div class="abs product" style="left:138px">
    <div class="thumb">PRODECT<br>IMAGE<br>HERE</div>
    <div class="name">LOCK WASHERS</div>
    <svg class="stars" width="60" height="9"><g fill="#0a4a78"><use href="#star" x="0" width="9" height="9"/><use href="#star" x="12" width="9" height="9"/><use href="#star" x="24" width="9" height="9"/><use href="#star" x="36" width="9" height="9"/></g><use href="#star" x="48" width="9" height="9" fill="#bbb"/></svg>
    <div class="order"><span class="price">$85</span><span class="buy">BUY</span></div>
  </div>
  <div class="abs product" style="left:233px">
    <div class="thumb">PRODECT<br>IMAGE<br>HERE</div>
    <div class="name">PINS</div>
    <svg class="stars" width="60" height="9"><g fill="#0a4a78"><use href="#star" x="0" width="9" height="9"/><use href="#star" x="12" width="9" height="9"/><use href="#star" x="24" width="9" height="9"/><use href="#star" x="36" width="9" height="9"/></g><use href="#star" x="48" width="9" height="9" fill="#bbb"/></svg>
    <div class="order"><span class="price">$85</span><span class="buy">BUY</span></div>
  </div>
  <div class="abs product" style="left:336px">
    <div class="thumb">PRODECT<br>IMAGE<br>HERE</div>
    <div class="name" style="margin-top:11px">STAMPINGS</div>
    <svg class="stars" width="60" height="9"><g fill="#0a4a78"><use href="#star" x="0" width="9" height="9"/><use href="#star" x="12" width="9" height="9"/><use href="#star" x="24" width="9" height="9"/><use href="#star" x="36" width="9" height="9"/></g><use href="#star" x="48" width="9" height="9" fill="#bbb"/></svg>
    <div class="order"><span class="price">$85</span><span class="buy">BUY</span></div>
  </div>
  <div class="abs product" style="left:432px">
    <div class="thumb">PRODECT<br>IMAGE<br>HERE</div>
    <div class="name" style="margin-top:11px">THREADED</div>
    <svg class="stars" width="60" height="9"><g fill="#0a4a78"><use href="#star" x="0" width="9" height="9"/><use href="#star" x="12" width="9" height="9"/><use href="#star" x="24" width="9" height="9"/><use href="#star" x="36" width="9" height="9"/></g><use href="#star" x="48" width="9" height="9" fill="#bbb"/></svg>
    <div class="order"><span class="price">$85</span><span class="buy">BUY</span></div>
  </div>

  <section class="abs intro">
    <h2>Tempor incididunt ut</h2>
    <p>Lorem ipsum dolor sit amet, consectetur adipisic ing elit, sed do eiusmod.</p>
  </section>

  <div class="abs circle blue" style="left:128px">CAPABILITIES</div>
  <div class="abs circle white" style="left:275px">QUOTE<br>REQUEST</div>
  <div class="abs circle blue" style="left:431px">QUALITY</div>

  <footer>
    <div class="abs footer"></div>
    <div class="abs foot-col" style="left:110px">
      <h3>About<span>US</span></h3><div class="rule"></div>
      <p>Lorem ipsum dolor sit amet, consectetur adipisicing elit, sed do eiusmod tempor incididunt ut labore et dolore magna aliqua.</p>
    </div>
    <div class="abs foot-col" style="left:266px">
      <h3>Quick<span>LINKS</span></h3><div class="rule"></div>
      <div class="links"><span>Home</span><span>About Us</span><span>products</span><span>Contact Us</span></div>
    </div>
    <div class="abs foot-col" style="left:418px">
      <h3>Social<span>MEDIA</span></h3><div class="rule"></div>
      <div class="social"><i></i><i></i><i></i><i></i><i></i></div>
    </div>
    <div class="abs legal">Terms &amp; Conditions | © 2017 KRV Boltmaster Group Coreplast® and Tapvane® are registered trademarks of RVMCO (Rivet Valley Manufacturing Co.). All other products and<br>names bearing these designations ™ ® are registered trademarks of Marrowfield Forge Holdings.</div>
  </footer>
</body>
</html>
```